NZ First of it's kind solutions directory and marketplace for busy Mums needs a business card design

We need a business card design for our new nationwide business in NZ (long term plans to go global). We provide solutions to the everyday challenges that busy Mums face by connecting them with quality communities and suppliers of carefully selected, relevant products and services. We sell direct via our online marketplace. The final design should communicate our values of inclusivity, quality and smart solutions. Colours should incorporate our logo colour palette of #477077 and #6ba8b2. Our website is at https://www.brightnestmums.example

Target Market(s)

busy Mums, Age 28 – 50, female, income over $100K, location main centres NZ primarily but NZ wide. Is likely juggling work or career with a young family. Probably had hobbies which have fallen by the wayside.
-Wants to succeed in her chosen career without compromising on family life
-to successfully juggle her career without feeling like she is compromising her children
- Is time poor, something always has to give and it’s generally her health (she’ll stay up late, get stressed)
- probably ex corporate or professional career. Has discretional income

Industry/Entity Type

Business

Contact Information for Business Card

Lena Forbisher, Founder, BrightNestMums.example (Strapline Tap; Gather; Sorted), 47 Kowhai Terrace, Ellerslie, Auckland 1051, New Zealand. Mob: 021 483 517 Ph: +64 (0)9 571 4860

Font styles to use
Other font styles liked:
• Raleway, and/or Architects Daughter

Colors
00a990
33b8a4
86cfc6
cfeae6

Requirements
Must have
• the above details, streamline. the logo and colours associated with those logos
Should not have
• foil or metallic colours

```html
<!DOCTYPE html>
<html lang="en">
<head>
<meta charset="utf-8">
<title>BrightNestMums business card</title>
<link rel="stylesheet" href="https://fonts.googleapis.com/css2?family=Roboto:wght@400;500;700&family=Roboto+Condensed:wght@700&display=swap">
<style>
  :root {
    --teal-dark: #477077;
    --teal-light: #6ba8b2;
    --card: #f1f1f1;
    --backdrop: #2b2b2b;
    --ink-grey: #4d4d4d;
    --white: #ffffff;
  }
  html, body {
    margin: 0;
    width: 1200px;
    height: 960px;
    overflow: hidden;
    background: var(--backdrop);
    font-family: "Roboto", Arial, sans-serif;
  }
  .canvas { position: relative; width: 1200px; height: 960px; }
  .card {
    position: absolute;
    width: 600px;
    height: 342px;
    border-radius: 22px;
    background: var(--card);
    overflow: hidden;
    box-shadow: 0 4px 10px rgba(0,0,0,0.45);
  }
  .card--front { left: 314px; top: 113px; }
  .card--back { left: 311px; top: 472px; }
  .wave { position: absolute; inset: 0; }

  .brand { position: absolute; display: flex; align-items: center; }
  .brand__dot { border-radius: 50%; background: var(--teal-dark); flex: none; }
  .brand__name { font-weight: 700; color: var(--teal-dark); letter-spacing: -0.5px; }

  .card--front .brand { left: 48px; top: 56px; gap: 12px; }
  .card--front .brand__dot { width: 32px; height: 32px; }
  .card--front .brand__name { font-size: 34px; }

  .contact {
    position: absolute;
    right: 32px;
    top: 156px;
    text-align: right;
    color: var(--white);
    font-size: 14.5px;
    line-height: 19px;
  }
  .contact__name {
    font-family: "Roboto Condensed", "Arial Narrow", sans-serif;
    font-weight: 700;
    font-size: 21px;
    line-height: 24px;
    color: var(--teal-light);
    letter-spacing: 0.3px;
  }
  .contact__role { font-weight: 500; font-size: 15px; line-height: 20px; margin-bottom: 12px; }
  .contact__address { margin-bottom: 10px; }
  .contact__line { display: flex; justify-content: flex-end; align-items: center; gap: 6px; }
  .contact__icon { width: 14px; height: 14px; flex: none; }

  .card--back .brand__mark {
    position: absolute;
    left: 22px; top: 100px;
    width: 170px; height: 170px;
    border-radius: 50%;
    background: var(--teal-dark);
  }
  .card--back .brand__name {
    position: absolute;
    right: 58px; top: 236px;
    font-size: 44px;
    line-height: 48px;
  }
  .strapline {
    position: absolute;
    right: 56px; top: 288px;
    font-size: 14px;
    color: var(--ink-grey);
    letter-spacing: 0.3px;
  }
</style>
</head>
<body>
<main class="canvas">
  <section class="card card--front">
    <svg class="wave" viewBox="0 0 600 342" width="600" height="342" aria-hidden="true">
      <path fill="var(--teal-light)" d="M0,228 C120,290 240,300 335,212 C425,128 485,58 560,62 C580,63 595,68 600,72 L600,342 L0,342 Z"/>
      <path fill="var(--teal-dark)" stroke="var(--white)" stroke-width="3" d="M0,256 C120,306 235,312 335,226 C425,146 485,76 560,78 C580,78 595,80 602,82 L602,344 L-2,344 Z"/>
    </svg>
    <div class="brand">
      <span class="brand__dot"></span>
      <span class="brand__name">BrightNestMums</span>
    </div>
    <div class="contact">
      <div class="contact__name">LENA FORBISHER</div>
      <div class="contact__role">FOUNDER</div>
      <div class="contact__address">47 Kowhai Terrace, Ellerslie<br>Auckland 1051, New Zealand.</div>
      <div class="contact__line">+64 (0)9 571 4860
        <svg class="contact__icon" viewBox="0 0 14 14" aria-hidden="true"><path fill="var(--teal-light)" d="M3,1 L5,4 L4,5.5 C5,7.5 6.5,9 8.5,10 L10,9 L13,11 L12,13 C6,13 1,8 1,2 Z"/></svg>
      </div>
      <div class="contact__line">021 483 517
        <svg class="contact__icon" viewBox="0 0 14 14" aria-hidden="true"><rect x="3.5" y="0.8" width="7" height="12.4" rx="1.2" fill="none" stroke="var(--teal-light)" stroke-width="1.4"/><rect x="5" y="2.5" width="4" height="7.5" fill="var(--teal-light)"/></svg>
      </div>
      <div class="contact__line">BrightNestMums.example
        <svg class="contact__icon" viewBox="0 0 14 14" aria-hidden="true"><circle cx="7" cy="7" r="6" fill="var(--teal-light)"/><path d="M1,7 H13 M7,1 C4,4 4,10 7,13 M7,1 C10,4 10,10 7,13" fill="none" stroke="var(--teal-dark)" stroke-width="0.9"/></svg>
      </div>
    </div>
  </section>

  <section class="card card--back">
    <span class="brand__mark"></span>
    <span class="brand__name">BrightNestMums</span>
    <span class="strapline">TAP; GATHER; SORTED</span>
  </section>
</main>
</body>
</html>
```